Velmora Freightway Solutions Business cards

Would like a very unique design catchy but professional for business cards. Please use log provided.Marlon WellsCeo and Founder TransCon Logistix Solutions1-888-913-3225mwells@tlsolutionsus.comwww.tlsolutionsus.com

```html
<!DOCTYPE html>
<html lang="en">
<head>
<meta charset="utf-8">
<title>Velmora Freightway Solutions – Business Cards</title>
<link href="https://fonts.googleapis.com/css2?family=Source+Sans+3:wght@300;400;600;700&display=swap" rel="stylesheet">
<style>
  :root {
    --page: #dcdcdc;
    --white: #ffffff;
    --paper: #f4f4f4;
    --blue: #1f6fbf;
    --blue-dark: #1a62ab;
    --red: #e0252b;
    --text-white: #ffffff;
  }
  * { margin: 0; padding: 0; box-sizing: border-box; }
  html, body {
    width: 1200px; height: 1176px; overflow: hidden;
    background: var(--page);
    font-family: "Source Sans 3", "Helvetica Neue", Arial, sans-serif;
  }
  .canvas { position: relative; width: 1200px; height: 1176px; }

  .card {
    position: absolute; left: 200px; width: 780px;
    border-radius: 22px; overflow: hidden;
    box-shadow: 0 4px 10px rgba(0,0,0,0.25);
  }

  /* Front */
  .card-front { top: 82px; height: 448px; background: var(--white); }
  .front-brand {
    position: absolute; left: 0; top: 0; width: 100%; height: 252px;
    background: linear-gradient(180deg, #ffffff, var(--paper));
    display: flex; align-items: center; justify-content: center;
  }
  .wordmark {
    color: var(--blue); font-weight: 700; text-align: center;
    font-size: 34px; line-height: 1.15; letter-spacing: 2px; text-transform: uppercase;
  }
  .wordmark small { display: block; font-size: 22px; letter-spacing: 5px; }
  .contact-band {
    position: absolute; left: 0; top: 252px; width: 100%; height: 136px;
    background: var(--blue);
  }
  .person {
    position: absolute; right: 414px; top: 38px; text-align: right; color: var(--text-white);
  }
  .person-name { font-size: 30px; font-weight: 300; letter-spacing: 0.5px; line-height: 1; }
  .person-name b { font-weight: 700; }
  .person-title { font-size: 19px; font-weight: 400; margin-top: 10px; }
  .divider {
    position: absolute; left: 390px; top: 24px; width: 2px; height: 92px; background: var(--red);
  }
  .contact-list { position: absolute; left: 408px; top: 24px; list-style: none; color: var(--text-white); }
  .contact-list li {
    display: flex; align-items: center; gap: 9px;
    font-size: 19px; height: 32.5px;
  }
  .contact-list svg { width: 18px; height: 18px; flex: none; }
  .address-band {
    position: absolute; left: 0; top: 392px; width: 100%; height: 56px;
    background: var(--red); color: var(--text-white);
    display: flex; align-items: center; justify-content: center; font-size: 19px;
  }

  /* Back */
  .card-back {
    top: 590px; height: 446px;
    background: linear-gradient(180deg, var(--blue), var(--blue-dark));
  }
  .back-wordmark {
    position: absolute; left: 0; top: 196px; width: 100%; text-align: center;
    color: var(--text-white); font-weight: 700; text-transform: uppercase;
    font-size: 42px; letter-spacing: 3px; line-height: 1.1;
  }
  .back-wordmark small { display: block; font-size: 26px; letter-spacing: 7px; }
  .back-url {
    position: absolute; left: 0; top: 372px; width: 100%; text-align: center;
    color: var(--text-white); font-size: 19px; letter-spacing: 4px;
  }
</style>
</head>
<body>
<main class="canvas">

  <section class="card card-front">
    <div class="front-brand">
      <div class="wordmark">Velmora Freightway<small>Solutions</small></div>
    </div>
    <div class="contact-band">
      <div class="person">
        <p class="person-name">DORIAN <b>PIKE</b></p>
        <p class="person-title">CEO AND FOUNDER</p>
      </div>
      <div class="divider"></div>
      <ul class="contact-list">
        <li>
          <svg viewBox="0 0 20 20" aria-hidden="true"><path fill="#e0252b" d="M2 8c0-3 4-5 8-5s8 2 8 5l-3 1-1-2H6L5 9 2 8zm3 2h10l2 7H3l2-7zm5 1.5a2.3 2.3 0 1 0 0 4.6 2.3 2.3 0 0 0 0-4.6z"/></svg>
          1-888-470-6158
        </li>
        <li>
          <svg viewBox="0 0 20 20" aria-hidden="true"><rect x="2" y="5" width="16" height="11" fill="#e0252b"/><path d="M2 5l8 6 8-6" stroke="#1f6fbf" stroke-width="1.4" fill="none"/></svg>
          dpike@vfwayroutes.com
        </li>
        <li>
          <svg viewBox="0 0 20 20" aria-hidden="true" fill="none" stroke="#e0252b" stroke-width="1.4"><circle cx="10" cy="10" r="7.5"/><ellipse cx="10" cy="10" rx="3.5" ry="7.5"/><path d="M2.5 10h15M4 6h12M4 14h12"/></svg>
          www.vfwayroutes.com
        </li>
      </ul>
    </div>
    <div class="address-band">2741 Calloway Ridge Rd, Atlanta, GA 30342</div>
  </section>

  <section class="card card-back">
    <div class="back-wordmark">Velmora Freightway<small>Solutions</small></div>
    <p class="back-url">www.vfwayroutes.com</p>
  </section>

</main>
</body>
</html>
```